Brisbane IT support business needs our first website

Hi All,

We are after a new website design for our IT solutions and support business.The business name is Harbourline Computing Services Group, or HCSG for short. We provide a range of solutions and services within the IT space.

I would like to utilize the two colours in our business logo I have uploaded.

I understand this is initially for the design only aspect of the site, but I would like to engage the winner to finish coding the website and finalize after also.

Target Market(s)

Other businesses owners and home users.

Industry/Entity Type

Business

Requirements
Must have
• Nice clean and functional design utilizing our business colours from the logo.

```html
<!DOCTYPE html>
<html lang="en">
<head>
<meta charset="utf-8">
<title>HCSG – Harbourline Computing Services Group</title>
<link rel="stylesheet" href="https://fonts.googleapis.com/css2?family=Lato:ital,wght@0,300;0,400;0,700;0,900;1,300;1,400&display=swap">
<style>
:root{
  --teal:#0d4b68;
  --teal-dark:#0a3a52;
  --orange:#f07f1e;
  --orange-dark:#e0701a;
  --ink:#333;
  --muted:#555;
  --light:#f4f4f4;
  --line:#dcdcdc;
  --white:#fff;
}
*{box-sizing:border-box;margin:0;padding:0}
html,body{width:1200px;height:2275px;overflow:hidden}
body{font-family:"Lato",Arial,sans-serif;color:var(--ink);background:var(--white);position:relative}
.abs{position:absolute}

/* header */
.site-header{position:absolute;left:0;top:0;width:1200px;height:133px;background:var(--white)}
.social-tab{position:absolute;right:120px;top:0;width:200px;height:36px;background:#1c1c1c;border-radius:0 0 24px 24px;display:flex;gap:10px;justify-content:center;align-items:center}
.social-tab span{width:22px;height:22px;border-radius:50%;background:#4d7fa6}
.social-tab span:last-child{background:var(--orange)}
.brand{position:absolute;left:133px;top:26px;display:flex;align-items:center;gap:16px}
.brand-mark{width:92px;height:92px;border-radius:50%;background:var(--teal)}
.brand-name{color:var(--orange);font-weight:700;font-size:44px;line-height:1;letter-spacing:1px}
.brand-full{color:var(--orange);font-weight:700;font-size:10.5px;line-height:1.25;width:150px;margin-top:5px;border-left:3px solid var(--orange);padding-left:6px}
.contact-top{position:absolute;right:133px;top:52px;text-align:right}
.contact-top .phone{font-size:22px;color:#222;display:flex;align-items:center;gap:10px;justify-content:flex-end}
.contact-top .mail{font-size:14px;color:#444;margin-top:14px;display:flex;align-items:center;gap:8px;justify-content:flex-end}

.main-nav{position:absolute;left:0;top:133px;width:1200px;height:47px;background:var(--teal);border-top:1px solid #1a5c7c}
.main-nav ul{list-style:none;display:flex;position:absolute;left:120px;top:0;height:47px}
.main-nav li{color:var(--white);font-size:14px;font-weight:400;height:47px;display:flex;align-items:center;padding:0 33px;border-right:1px solid #2a6a88}
.main-nav li:last-child{border-right:0}
.main-nav li.active span{background:var(--orange);padding:8px 14px;border-radius:2px}

/* hero */
.hero{position:absolute;left:0;top:180px;width:1200px;height:525px;background:radial-gradient(ellipse at 62% 55%,#5a4630 0%,#2a2420 25%,#121416 55%,#07090b 100%)}
.hero h1{position:absolute;left:133px;top:185px;color:var(--white);font-weight:400;font-style:italic;font-size:36px;line-height:48px}
.hero-arrow{position:absolute;top:228px;width:60px;height:60px;border-radius:50%;border:2px solid #777;background:rgba(0,0,0,.5);display:flex;align-items:center;justify-content:center}

/* services */
.services{position:absolute;left:0;top:705px;width:1200px;height:395px}
.section-title{display:flex;align-items:center;justify-content:center;gap:12px;font-size:30px;font-weight:400;color:var(--teal)}
.section-title .mini-mark{width:46px;height:46px;border-radius:50%;background:var(--teal)}
.section-title em{font-style:normal;color:var(--orange)}
.services .section-title{position:absolute;left:0;right:0;top:22px}
.title-rule{position:absolute;left:245px;width:710px;top:78px;height:1px;background:var(--line)}
.title-stars{position:absolute;left:577px;top:70px;display:flex;gap:4px}
.service-card{position:absolute;top:101px;width:216px;height:233px;background:var(--light);text-align:center}
.service-card .icon{width:90px;height:90px;border-radius:50%;background:var(--teal);border:4px solid var(--white);box-shadow:0 0 0 1px #ccc;margin:-4px auto 0;display:flex;align-items:center;justify-content:center}
.service-card h3{color:var(--orange);font-size:19px;font-weight:400;margin-top:14px}
.service-card p{font-size:13px;line-height:19px;color:#444;margin:8px 14px 0}
.read-more{position:absolute;left:58px;bottom:-6px;width:100px;height:22px;background:var(--teal);color:var(--white);font-size:10.5px;font-weight:700;display:flex;align-items:center;justify-content:center;border-radius:2px}
.side-arrow{position:absolute;top:228px;font-size:24px;font-weight:900;color:#111}

/* welcome */
.welcome{position:absolute;left:0;top:1100px;width:1200px;height:280px;background:#f5f5f5}
.welcome .section-title{position:absolute;left:133px;top:22px;justify-content:flex-start;font-size:28px}
.welcome .rule{position:absolute;left:133px;top:82px;width:607px;height:1px;background:var(--line)}
.welcome p{position:absolute;left:133px;width:607px;font-size:12.6px;line-height:22px;color:#333}
.welcome-photo{position:absolute;left:768px;top:34px;width:299px;height:222px;background:radial-gradient(ellipse at 45% 45%,#9fd4f7 0%,#2f7fc0 35%,#0b2f5c 75%,#061a36 100%);border-radius:3px}

/* three columns */
.info-cols{position:absolute;left:0;top:1380px;width:1200px;height:355px}
.col{position:absolute;top:32px}
.col h4{font-size:21px;font-weight:700;color:var(--teal);padding-bottom:10px;border-bottom:1px solid var(--line)}
.col h4 em{font-style:normal;color:var(--orange);font-weight:400}
.col-arrows{position:absolute;right:0;top:6px;font-size:14px;color:#333}
.why li{list-style:none;display:flex;gap:14px;font-size:13px;line-height:19px;color:#333;padding:12px 0;border-bottom:1px dotted #ccc}
.why li svg{flex:none;margin-top:4px}
.news-item{display:flex;gap:12px;margin-top:16px}
.date{width:46px;flex:none;text-align:center}
.date b{display:block;background:var(--orange);color:var(--white);font-size:20px;padding:3px 0}
.date span{display:block;background:#e5e5e5;color:#333;font-size:13px;font-weight:700;padding:3px 0}
.news-item h5{color:var(--teal);font-size:13.5px;font-weight:700}
.news-item p{font-size:13px;line-height:19px;color:#444;margin-top:3px}
.quote{margin-top:16px;background:#efefef;height:168px;padding:16px 16px 0 30px;font-size:12.3px;font-style:italic;line-height:20.5px;color:#333;position:relative}
.quote::before{content:"\201C";position:absolute;left:10px;top:2px;font-size:44px;color:#ccc;font-style:normal}
.avatar{position:absolute;right:10px;top:186px;width:86px;height:86px;border-radius:50%;background:linear-gradient(#6b7a88,#2b3a48);border:4px solid var(--white);box-shadow:0 1px 3px rgba(0,0,0,.3)}
.author{position:absolute;left:18px;top:254px;font-size:11.5px;font-weight:700;color:var(--orange)}

/* clients */
.clients{position:absolute;left:0;top:1735px;width:1200px;height:180px;background:var(--teal)}
.clients h2{position:absolute;left:0;right:0;top:18px;text-align:center;color:var(--white);font-weight:400;font-size:28px}
.clients .rule{position:absolute;left:460px;width:280px;top:62px;height:1px;background:#3d7591}
.client-logo{position:absolute;top:72px;height:76px;background:var(--white);display:flex;align-items:center;justify-content:center;gap:7px;font-size:17px;font-weight:700;color:#333;white-space:nowrap}
.client-logo i{width:12px;height:12px;background:#333;display:block;flex:none}

/* footer */
.site-footer{position:absolute;left:0;top:1915px;width:1200px;height:300px;background:var(--orange)}
.site-footer h4{color:var(--white);font-size:19px;font-weight:700}
.newsletter{position:absolute;left:133px;top:28px;width:210px}
.newsletter p{color:var(--white);font-size:12.5px;line-height:19px;margin-top:14px}
.field{background:var(--white);height:32px;margin-top:12px;font-size:12px;color:#444;padding:9px 12px}
.subscribe{display:inline-block;background:var(--teal);color:var(--white);font-size:12px;font-weight:700;padding:9px 12px;margin-top:18px;border-radius:2px}
.quick-links{position:absolute;left:389px;top:0;width:380px;height:300px;background:var(--orange-dark);box-shadow:-6px 0 10px -6px rgba(0,0,0,.25),6px 0 10px -6px rgba(0,0,0,.25);padding:28px 13px}
.quick-links ul{list-style:none;position:absolute;top:72px;font-size:12.5px;color:var(--white);line-height:29px}
.quick-links li::before{content:"\2022";margin-right:10px}
.footer-mark{position:absolute;left:265px;top:70px;width:92px;height:92px;border-radius:50%;background:var(--teal-dark)}
.contact-box{position:absolute;left:13px;top:199px;width:354px;height:61px;background:var(--teal);border-radius:4px;display:flex;align-items:center;padding:0 14px;gap:14px;color:var(--white);white-space:nowrap}
.contact-box b{font-size:16px;font-weight:700}
.contact-box svg{flex:none}
.contact-box span{font-size:23px}
.location{position:absolute;left:813px;top:28px}
.map{position:absolute;left:0;top:42px;width:240px;height:176px;background:linear-gradient(135deg,#e7e3d6,#d6dfc9 55%,#c9d8e4);border-radius:3px}

.bottom-bar{position:absolute;left:0;top:2215px;width:1200px;height:60px;background:var(--orange);border-top:1px solid #f59a4b}
.bottom-bar small{position:absolute;left:133px;top:22px;color:var(--white);font-size:12px}
.footer-social{position:absolute;right:133px;top:15px;display:flex;gap:10px}
.footer-social span{width:28px;height:28px;border-radius:50%;background:var(--teal)}
</style>
</head>
<body>

<header class="site-header">
  <div class="social-tab"><span></span><span></span><span></span><span></span></div>
  <div class="brand">
    <div class="brand-mark"></div>
    <div>
      <div class="brand-name">HCSG</div>
      <div class="brand-full">HARBOURLINE COMPUTING SERVICES GROUP</div>
    </div>
  </div>
  <div class="contact-top">
    <div class="phone">
      <svg width="26" height="26" viewBox="0 0 26 26"><circle cx="13" cy="13" r="11.5" fill="none" stroke="#f07f1e" stroke-width="2"/><path d="M9 7l3 3-2 2c1 2 2 3 4 4l2-2 3 3-2 2c-5-1-9-5-10-10z" fill="#f07f1e"/></svg>
      07 5550 1842
    </div>
    <div class="mail">
      <svg width="20" height="14" viewBox="0 0 20 14"><rect width="20" height="14" rx="1" fill="#f07f1e"/><path d="M1 1l9 7 9-7" fill="none" stroke="#fff" stroke-width="1.5"/></svg>
      info@harbourline-cs.example
    </div>
  </div>
</header>

<nav class="main-nav">
  <ul>
    <li class="active"><span>HOME</span></li>
    <li>ABOUT US</li>
    <li>SERVICES</li>
    <li>TECHNOLOGY</li>
    <li>SOLUTIONS</li>
    <li>SUPPORT</li>
    <li>CONTACT US</li>
  </ul>
</nav>

<section class="hero">
  <div class="abs" role="img" aria-label="Open hand in a business suit holding glowing IT service icons" style="inset:0"></div>
  <h1>We provide a range<br>of solutions and services<br>within the IT space.</h1>
  <div class="hero-arrow" style="left:45px"><svg width="18" height="28" viewBox="0 0 18 28"><path d="M14 2L3 14l11 12" fill="none" stroke="#fff" stroke-width="2"/></svg></div>
  <div class="hero-arrow" style="left:1087px"><svg width="18" height="28" viewBox="0 0 18 28"><path d="M4 2l11 12L4 26" fill="none" stroke="#fff" stroke-width="2"/></svg></div>
</section>

<section class="services">
  <h2 class="section-title"><span class="mini-mark"></span><span><em>OUR</em> SERVICES</span></h2>
  <div class="title-rule"></div>
  <div class="title-stars">
    <svg width="46" height="14" viewBox="0 0 46 14"><polygon points="7,1 9,5 13,5 10,8 11,12 7,10 3,12 4,8 1,5 5,5" fill="#bbb"/><polygon points="23,0 25.5,5 31,5 27,8.5 28.5,14 23,11 17.5,14 19,8.5 15,5 20.5,5" fill="#0d4b68"/><polygon points="39,1 41,5 45,5 42,8 43,12 39,10 35,12 36,8 33,5 37,5" fill="#bbb"/></svg>
  </div>
  <div class="side-arrow" style="left:84px">&#8249;</div>
  <div class="side-arrow" style="left:1104px">&#8250;</div>

  <div class="service-card" style="left:133px">
    <div class="icon"><svg width="46" height="46" viewBox="0 0 46 46"><circle cx="18" cy="26" r="10" fill="none" stroke="#f07f1e" stroke-width="6" stroke-dasharray="4 3"/><circle cx="33" cy="13" r="6" fill="none" stroke="#f07f1e" stroke-width="4" stroke-dasharray="3 2"/></svg></div>
    <h3>Website Services</h3>
    <p>Lorem ipsum dolor sit amet, consectetu adipiscing elit, sed diam nonummy nibh euismod</p>
    <div class="read-more">READ MORE &raquo;</div>
  </div>
  <div class="service-card" style="left:373px">
    <div class="icon"><svg width="46" height="46" viewBox="0 0 46 46"><path d="M8 38L32 14M14 8l24 30" stroke="#fff" stroke-width="5" stroke-linecap="round"/><circle cx="34" cy="11" r="6" fill="none" stroke="#fff" stroke-width="3"/></svg></div>
    <h3>Hardware &amp; Sfotware</h3>
    <p>Lorem ipsum dolor sit amet, consectetu adipiscing elit, sed diam nonummy nibh euismod</p>
    <div class="read-more">READ MORE &raquo;</div>
  </div>
  <div class="service-card" style="left:612px">
    <div class="icon"><svg width="50" height="50" viewBox="0 0 50 50"><circle cx="25" cy="25" r="13" fill="#fff"/><circle cx="25" cy="25" r="20" fill="none" stroke="#fff" stroke-width="1.5" stroke-dasharray="3 4"/><text x="25" y="29" text-anchor="middle" font-family="Lato,sans-serif" font-size="10" font-weight="700" fill="#0d4b68">SEO</text></svg></div>
    <h3>SEO Services</h3>
    <p>Lorem ipsum dolor sit amet, consectetu adipiscing elit, sed diam nonummy nibh euismod</p>
    <div class="read-more">READ MORE &raquo;</div>
  </div>
  <div class="service-card" style="left:853px">
    <div class="icon"><svg width="48" height="44" viewBox="0 0 48 44"><rect x="3" y="3" width="42" height="28" rx="2" fill="#fff"/><rect x="19" y="31" width="10" height="6" fill="#fff"/><rect x="12" y="37" width="24" height="3" fill="#fff"/><path d="M14 24a6 6 0 0 1 4-10 8 8 0 0 1 15 2 5 5 0 0 1 1 8z" fill="#0d4b68"/></svg></div>
    <h3>Software Development</h3>
    <p>Lorem ipsum dolor sit amet, consectetu adipiscing elit, sed diam nonummy nibh euismod</p>
    <div class="read-more">READ MORE &raquo;</div>
  </div>
</section>

<section class="welcome">
  <h2 class="section-title"><span class="mini-mark"></span><span>WELCOME TO <em>HCSG</em></span></h2>
  <div class="rule"></div>
  <p style="top:98px">Lorem ipsum dolor sit amet, consectetuer adipiscing elit, sed diam nonummy nibh euism od tincidunt ut laoreet dolore magna aliquam erat volutpat. Ut wisi enim ad minim venia m, quis nostrud exerci in amet ullamcorper suscipit lobortis nisl ut aliquip ex ea comsed diam nonummy nibh euism od tincidunt uopre laoreet dolore magna aliquam erat volutpat.</p>
  <p style="top:190px">Lorem ipsum dolor sit amet, consectetuer adipiscing elit, sed diam nonummy nibh euism od tincidunt ut in laoreet dolore magna aliquam erat volutpat. Ut wisi enim ad minim venia m, quis nostrud exerci tationperq ullamcorper suscipit lobortis nisl ut..</p>
  <div class="welcome-photo" role="img" aria-label="Hand touching a glowing world map with network connections"></div>
</section>

<section class="info-cols">
  <div class="col why" style="left:133px;width:284px">
    <h4>Why <em>Choose Us</em></h4>
    <ul>
      <li><svg width="14" height="14" viewBox="0 0 14 14"><path d="M7 0l2 3H5zM7 14l2-3H5zM0 7l3-2v4zM14 7l-3-2v4z" fill="#f07f1e"/><circle cx="7" cy="7" r="1.5" fill="#f07f1e"/></svg>Lorem ipsum dolor sit tetu adipiscing elised diam nonummy nibh euismod</li>
      <li><svg width="14" height="14" viewBox="0 0 14 14"><path d="M7 0l2 3H5zM7 14l2-3H5zM0 7l3-2v4zM14 7l-3-2v4z" fill="#f07f1e"/><circle cx="7" cy="7" r="1.5" fill="#f07f1e"/></svg>Lorem ipsum dolor sit tetu adipiscing elised diam nonummy nibh euismod</li>
      <li><svg width="14" height="14" viewBox="0 0 14 14"><path d="M7 0l2 3H5zM7 14l2-3H5zM0 7l3-2v4zM14 7l-3-2v4z" fill="#f07f1e"/><circle cx="7" cy="7" r="1.5" fill="#f07f1e"/></svg>Lorem ipsum dolor sit tetu adipiscing elsied</li>
      <li><svg width="14" height="14" viewBox="0 0 14 14"><path d="M7 0l2 3H5zM7 14l2-3H5zM0 7l3-2v4zM14 7l-3-2v4z" fill="#f07f1e"/><circle cx="7" cy="7" r="1.5" fill="#f07f1e"/></svg>Ktu adipiscing elitsied orem ipsum dolor sit</li>
      <li style="border-bottom:0"><svg width="14" height="14" viewBox="0 0 14 14"><path d="M7 0l2 3H5zM7 14l2-3H5zM0 7l3-2v4zM14 7l-3-2v4z" fill="#f07f1e"/><circle cx="7" cy="7" r="1.5" fill="#f07f1e"/></svg>Ktu adipiscing elitsied orem ipsum dolor sit</li>
    </ul>
  </div>

  <div class="col" style="left:461px;width:284px">
    <h4>Latest <em>News</em></h4>
    <div class="col-arrows">&#9664; &#9654;</div>
    <div class="news-item"><div class="date"><b>31</b><span>OCT</span></div><div><h5>Lorem ipsum dolor sit ametcons...</h5><p>Sed diam nonny nibh eumod tincidun ut laoreet dolore magna aliquam.</p></div></div>
    <div class="news-item" style="margin-top:24px"><div class="date"><b>29</b><span>OCT</span></div><div><h5>Lorem ipsum dolor sit ametcons...</h5><p>Sed diam nonny nibh eumod tincidun ut laoreet dolore magna aliquam.</p></div></div>
    <div class="news-item" style="margin-top:24px"><div class="date"><b>27</b><span>OCT</span></div><div><h5>Lorem ipsum dolor sit ametcons...</h5><p>Sed diam nonny nibh eumod tincidun ut laoreet dolore magna aliquam.</p></div></div>
  </div>

  <div class="col" style="left:787px;width:284px;height:290px">
    <h4>Client <em>Testimonials</em></h4>
    <div class="col-arrows">&#9664; &#9654;</div>
    <div class="quote">Lorem ipsum dolor sit amet consctuerepf adipiscing elit, sed diam nonny nibh euismodg tincidunt ut laoreet dolore magna aliquam eratg volutpat. Ut wisi enim ad minim veniam, quis nostrud exerci tation ullamcorper suscipit tation ullcorper suscipit tation.</div>
    <div class="avatar" role="img" aria-label="Client portrait"></div>
    <div class="author">MR. QUIS NOSTRUD EXERCI</div>
  </div>
</section>

<section class="clients">
  <h2>Our Clients</h2>
  <div class="rule"></div>
  <div class="client-logo" style="left:133px;width:147px"><i></i>Meridian Labs</div>
  <div class="client-logo" style="left:305px;width:165px">Northgate Co.</div>
  <div class="client-logo" style="left:495px;width:198px">Tallwood</div>
  <div class="client-logo" style="left:720px;width:143px"><i style="border-radius:50%"></i>Corvane</div>
  <div class="client-logo" style="left:886px;width:181px">Ledgerly</div>
</section>

<footer class="site-footer">
  <div class="newsletter">
    <h4>Newsletter Signup</h4>
    <p>Lorem ipsum dolor sit amet, consectetu er adipiscing elit, sed</p>
    <div class="field">Name</div>
    <div class="field">Email</div>
    <div class="subscribe">Subscribe</div>
  </div>
  <div class="quick-links">
    <h4>Quick Links</h4>
    <ul style="left:13px"><li>Home</li><li>About Us</li><li>Services</li><li>Technology</li></ul>
    <ul style="left:133px"><li>Solutions</li><li>Support</li><li>Contact Us</li></ul>
    <div class="footer-mark"></div>
    <div class="contact-box">
      <b>CONTACT US</b>
      <svg width="30" height="34" viewBox="0 0 30 34"><rect width="30" height="34" rx="4" fill="#555"/><path d="M10 7l4 4-2 3c1 3 3 5 6 6l2-2 4 4-3 3c-8-1-13-7-14-14z" fill="#ddd"/></svg>
      <span>07 5550 1842</span>
    </div>
  </div>
  <div class="location">
    <h4>Location Map</h4>
    <div class="map" role="img" aria-label="Street map showing the office location"></div>
  </div>
</footer>

<div class="bottom-bar">
  <small>&copy; 2014 HCSG. All Rights Reserved.</small>
  <div class="footer-social"><span></span><span></span><span></span><span style="background:var(--orange-dark)"></span></div>
</div>

</body>
</html>
```